Website Design for recruiting company

We need a homepage mockup for a recruiting company focused on the legal industry. Use your creative talent to come up with something visually appeal and professional for this web-site.

We'd really like to see the maze from the logo incorporated into the design somehow. Please use the website mockup provided as inspiration for this project. We really like the layout and photos!

Target Market(s)

lawyers

Industry/Entity Type

Legal

Number of Pages Required

1 page

Font styles to use
Sans Serif

```html
<!DOCTYPE html>
<html lang="en">
<head>
<meta charset="utf-8">
<title>Northgate Legal Search</title>
<link href="https://fonts.googleapis.com/css2?family=Lato:wght@300;400;700&display=swap" rel="stylesheet">
<style>
:root{
  --plum:#5f5063;
  --plum-dark:#4f4253;
  --ink:#2f2f33;
  --muted:#6b6b70;
  --mist:#e8e9e5;
  --white:#ffffff;
  --line:#b9b0bb;
}
*{box-sizing:border-box;margin:0;padding:0}
html,body{width:1200px;height:2733px;overflow:hidden}
body{font-family:'Lato',sans-serif;color:var(--ink);background:var(--white);position:relative}
a{color:inherit;text-decoration:none}
.arrow{display:inline-block;vertical-align:middle;margin-left:8px}

/* hero */
.hero{position:absolute;left:0;top:0;width:1200px;height:658px;overflow:hidden}
.hero-photo{position:absolute;inset:0;background:
  radial-gradient(ellipse 260px 300px at 640px 300px,rgba(70,90,80,.55),transparent 70%),
  radial-gradient(ellipse 300px 420px at 1080px 330px,rgba(150,170,195,.55),transparent 70%),
  linear-gradient(100deg,#2e2e31 0%,#444245 35%,#625c58 58%,#7f7973 78%,#9d9892 100%)}
.hero-shade{position:absolute;inset:0;background:linear-gradient(90deg,rgba(20,20,24,.5),rgba(20,20,24,0) 60%)}
.brand{position:absolute;left:78px;top:22px;display:flex;align-items:center;gap:10px;color:var(--white);font-weight:300;font-size:24px;letter-spacing:.3px}
.brand-mark{width:76px;height:76px;border-radius:50%;border:3px solid rgba(255,255,255,.85)}
.nav{position:absolute;top:44px;left:477px;display:flex;gap:39px;font-size:15px;font-weight:700;color:var(--white);letter-spacing:.2px}
.nav a.active{border-bottom:2px solid var(--white);padding-bottom:7px}
.hero-copy{position:absolute;left:137px;top:248px;color:var(--white)}
.hero-copy h1{font-size:43px;font-weight:700;line-height:50px;letter-spacing:.2px}
.hero-copy p{margin-top:20px;font-size:17px;line-height:24px;width:430px}
.btn{display:inline-flex;align-items:center;justify-content:center;background:var(--plum);color:var(--white);font-weight:700;text-transform:uppercase}
.hero-copy .btn{margin-top:30px;width:206px;height:49px;font-size:18px}
.dots{position:absolute;left:1106px;top:310px;display:flex;flex-direction:column;gap:10px}
.dots span{width:13px;height:13px;border-radius:50%;background:var(--white)}
.dots span.on{background:transparent;border:2px solid var(--white)}

/* about */
.about{position:absolute;left:0;top:658px;width:1200px;height:465px;background:var(--white)}
.about-photo{position:absolute;left:0;top:0;width:596px;height:465px;background:
  radial-gradient(ellipse 200px 240px at 150px 300px,rgba(90,140,200,.6),transparent 70%),
  linear-gradient(135deg,#cfc6b8 0%,#b7b3ab 30%,#8fa3b8 55%,#45505e 100%)}
.about-copy{position:absolute;left:655px;top:76px;width:466px}
.section-title{font-size:35px;font-weight:700;letter-spacing:.3px;text-transform:uppercase}
.about-copy p{margin-top:22px;font-size:16.5px;line-height:31px;color:var(--muted)}
.btn-outline{display:inline-flex;align-items:center;justify-content:center;margin-top:28px;width:176px;height:52px;border:2px solid var(--ink);font-size:16px;font-weight:700;color:var(--muted);text-transform:uppercase}

/* news */
.news{position:absolute;left:0;top:1123px;width:1200px;height:642px;background:var(--mist)}
.news .section-title{text-align:center;margin-top:65px;font-size:31px}
.cards{position:absolute;left:43px;top:137px;display:flex;gap:17px}
.card{width:212px;height:338px;background:var(--white);position:relative}
.card-photo{height:159px}
.card-icon{position:absolute;left:24px;top:130px;width:60px;height:60px;border-radius:50%;background:var(--white);display:flex;align-items:center;justify-content:center;box-shadow:0 1px 3px rgba(0,0,0,.15)}
.card-body{padding:42px 8px 0 26px}
.card h3{font-size:15px;font-weight:700;line-height:20px}
.card p{margin-top:14px;font-size:12px;line-height:19px;color:var(--muted);padding-right:10px}
.card .more{display:inline-flex;align-items:center;margin-top:12px;font-size:12.5px;font-weight:700;color:#4a4a4e}
.news .btn{position:absolute;left:493px;top:520px;width:217px;height:51px;font-size:19px}

/* employers */
.employers{position:absolute;left:0;top:1765px;width:1200px;height:482px;overflow:hidden}
.employers-photo{position:absolute;inset:0;background:
  radial-gradient(ellipse 220px 300px at 470px 230px,rgba(120,125,135,.55),transparent 70%),
  linear-gradient(90deg,#6c7f92 0%,#55636f 35%,#3e4b58 60%,#3a4550 100%)}
.employers-copy{position:absolute;left:656px;top:103px;width:470px;color:var(--white)}
.employers-copy h2{font-size:31px;font-weight:700;text-transform:uppercase}
.employers-copy p{margin-top:18px;font-size:18.5px;line-height:29px}
.employers-copy h4{margin-top:28px;font-size:20.5px;font-weight:700;text-transform:uppercase}
.employers-copy .btn{margin-top:12px;width:178px;height:44px;font-size:16px}

/* footer */
.footer{position:absolute;left:0;top:2247px;width:1200px;height:486px;background:var(--plum);color:var(--white)}
.footer .brand{left:160px;top:44px;font-size:22px;color:#ece6ee}
.footer .brand-mark{width:76px;height:76px}
.footer-rule{position:absolute;left:498px;top:84px;width:336px;border-top:1px solid var(--line)}
.social{position:absolute;left:854px;top:64px;display:flex;gap:5px}
.social span{width:41px;height:41px;border-radius:50%;border:2px solid var(--white)}
.cols{position:absolute;left:170px;top:180px;display:flex}
.col h5{font-size:22px;font-weight:400;margin-bottom:14px}
.col li{list-style:none;font-size:15.5px;line-height:35.5px;padding-left:4px;color:#f1ecf2}
.col.c1{width:251px}.col.c2{width:234px}.col.c3{width:200px}
.contact li{display:flex;align-items:center;gap:10px}
.footer-line{position:absolute;left:156px;top:432px;width:878px;border-top:1px solid var(--line)}
.copyright{position:absolute;left:0;width:1200px;top:457px;text-align:center;font-size:13px;color:#b9afbb}
</style>
</head>
<body>

<header class="hero">
  <div class="hero-photo" role="img" aria-label="Smiling man in glasses shaking hands with a woman across an office desk"></div>
  <div class="hero-shade"></div>
  <a class="brand" href="#"><span class="brand-mark"></span>northgate legal search</a>
  <nav class="nav">
    <a class="active" href="#">ABOUT US</a>
    <a href="#">WHAT'S NEW</a>
    <a href="#">FOR EMPLOYERS</a>
    <a href="#">IN HOUSE</a>
    <a href="#">CONTACT US</a>
  </nav>
  <div class="hero-copy">
    <h1>Start Here, Let Our<br>Experience Guide You</h1>
    <p>Curabitur metus ipsum luctus eu malesuada ut tincidunt sed diam vdisse risus nibh ultricies eu volutpat</p>
    <a class="btn" href="#">Learn More<svg class="arrow" width="22" height="14" viewBox="0 0 22 14"><path d="M1 7h19M14 1l6 6-6 6" fill="none" stroke="currentColor" stroke-width="2"/></svg></a>
  </div>
  <div class="dots"><span class="on"></span><span></span><span></span><span></span></div>
</header>

<section class="about">
  <div class="about-photo" role="img" aria-label="Two smiling businessmen in a meeting with a laptop"></div>
  <div class="about-copy">
    <h2 class="section-title">About Us</h2>
    <p>Northgate Legal Search focuses on the permanent placement of attorneys with law firms and corporations in the New England area. Founded in 1982, Northgate Legal Search is the oldest attorney search firm in New England, and is ranked the number one legal recruiter in New England in the most recent survey conducted by The Counsel Review.</p>
    <a class="btn-outline" href="#">Learn More<svg class="arrow" width="18" height="12" viewBox="0 0 18 12"><path d="M1 6h15M11 1l5 5-5 5" fill="none" stroke="currentColor" stroke-width="1.6"/></svg></a>
  </div>
</section>

<section class="news">
  <h2 class="section-title">What’s New</h2>
  <div class="cards">
    <article class="card">
      <div class="card-photo" role="img" aria-label="Team meeting around a table with a whiteboard" style="background:linear-gradient(135deg,#d9d6d0,#8b8f96)"></div>
      <div class="card-icon"><svg width="30" height="30" viewBox="0 0 30 30" fill="none" stroke="#555" stroke-width="1.4"><circle cx="15" cy="12" r="7"/><path d="M12 19v4h6v-4M12 26h6"/></svg></div>
      <div class="card-body"><h3>Praesent sit amet est In dictum eu dictum</h3><p>Etiam eleifend metus vitae ad-ipiscing semper mauris</p><a class="more" href="#">CLICK HERE<svg class="arrow" width="20" height="12" viewBox="0 0 20 12"><path d="M1 6h17M13 1l5 5-5 5" fill="none" stroke="currentColor" stroke-width="1.5"/></svg></a></div>
    </article>
    <article class="card">
      <div class="card-photo" role="img" aria-label="Colleagues talking in a dim office" style="background:linear-gradient(135deg,#6f6a66,#3d3b3c)"></div>
      <div class="card-icon"><svg width="30" height="30" viewBox="0 0 30 30" fill="none" stroke="#555" stroke-width="1.4"><rect x="5" y="10" width="20" height="14" rx="2"/><path d="M11 10V7h8v3M5 16h20"/></svg></div>
      <div class="card-body"><h3>Aliquam nec erat at purus interdum</h3><p>Etiam eleifend metus vitae ad-ipiscing semper mauris</p><a class="more" href="#">CLICK HERE<svg class="arrow" width="20" height="12" viewBox="0 0 20 12"><path d="M1 6h17M13 1l5 5-5 5" fill="none" stroke="currentColor" stroke-width="1.5"/></svg></a></div>
    </article>
    <article class="card">
      <div class="card-photo" role="img" aria-label="Two men reviewing documents together" style="background:linear-gradient(135deg,#c9cfd6,#6d7d90)"></div>
      <div class="card-icon"><svg width="30" height="30" viewBox="0 0 30 30" fill="none" stroke="#555" stroke-width="1.4"><path d="M9 26v-6c-3-2-4-5-3-8 1-4 5-6 9-6 5 0 8 4 8 8l2 4h-3v4h-4v4"/><circle cx="15" cy="12" r="3"/></svg></div>
      <div class="card-body"><h3>Curabitur vel mi sit amet magna malesuada</h3><p>Etiam eleifend metus vitae ad-ipiscing semper mauris</p><a class="more" href="#">CLICK HERE<svg class="arrow" width="20" height="12" viewBox="0 0 20 12"><path d="M1 6h17M13 1l5 5-5 5" fill="none" stroke="currentColor" stroke-width="1.5"/></svg></a></div>
    </article>
    <article class="card">
      <div class="card-photo" role="img" aria-label="Two businessmen looking at a phone" style="background:linear-gradient(135deg,#b4bcc6,#3e4856)"></div>
      <div class="card-icon"><svg width="30" height="30" viewBox="0 0 30 30" fill="none" stroke="#555" stroke-width="1.4"><ellipse cx="15" cy="8" rx="9" ry="3"/><path d="M6 8v14c0 2 4 3 9 3s9-1 9-3V8M6 15c0 2 4 3 9 3s9-1 9-3"/></svg></div>
      <div class="card-body"><h3>Mauris neque metus malesuada ultrici</h3><p>Etiam eleifend metus vitae ad-ipiscing semper mauris</p><a class="more" href="#">CLICK HERE<svg class="arrow" width="20" height="12" viewBox="0 0 20 12"><path d="M1 6h17M13 1l5 5-5 5" fill="none" stroke="currentColor" stroke-width="1.5"/></svg></a></div>
    </article>
    <article class="card">
      <div class="card-photo" role="img" aria-label="Smiling woman working at a laptop" style="background:linear-gradient(135deg,#e2ddd6,#8a7d72)"></div>
      <div class="card-icon"><svg width="30" height="30" viewBox="0 0 30 30" fill="none" stroke="#555" stroke-width="1.4"><path d="M7 18v-4a8 8 0 0 1 16 0v4"/><rect x="5" y="17" width="4" height="7" rx="1"/><rect x="21" y="17" width="4" height="7" rx="1"/></svg></div>
      <div class="card-body"><h3>Praesent sit amet est In dictum eu dictum</h3><p>Etiam eleifend metus vitae ad-ipiscing semper mauris</p><a class="more" href="#">CLICK HERE<svg class="arrow" width="20" height="12" viewBox="0 0 20 12"><path d="M1 6h17M13 1l5 5-5 5" fill="none" stroke="currentColor" stroke-width="1.5"/></svg></a></div>
    </article>
  </div>
  <a class="btn" href="#">Search Jobs<svg class="arrow" width="22" height="14" viewBox="0 0 22 14"><path d="M1 7h19M14 1l6 6-6 6" fill="none" stroke="currentColor" stroke-width="2"/></svg></a>
</section>

<section class="employers">
  <div class="employers-photo" role="img" aria-label="Smiling businessman in a grey suit gesturing during a conversation"></div>
  <div class="employers-copy">
    <h2>For Employers</h2>
    <p>Our unparalleled recruiting industry and legal experience have generated an extensive network of contacts throughout the legal community.</p>
    <h4>Find the Right Candidate</h4>
    <a class="btn" href="#">Start Here<svg class="arrow" width="20" height="13" viewBox="0 0 20 13"><path d="M1 6.5h17M12 1l6 5.5-6 5.5" fill="none" stroke="currentColor" stroke-width="1.8"/></svg></a>
  </div>
</section>

<footer class="footer">
  <a class="brand" href="#"><span class="brand-mark"></span>northgate legal search</a>
  <div class="footer-rule"></div>
  <div class="social"><span></span><span></span><span></span><span></span></div>
  <div class="cols">
    <div class="col c1"><h5>Quick Links</h5><ul><li>Law Firms</li><li>Associate</li><li>Partner</li><li>Other</li></ul></div>
    <div class="col c2"><h5>Resources</h5><ul><li>Regional</li><li>What's New</li><li>About Us</li><li>For Employers</li></ul></div>
    <div class="col c3"><h5>Links</h5><ul><li>Law Firms</li><li>Submit Resume</li><li>Contact Us</li></ul></div>
    <div class="col contact"><h5>Contact Us</h5><ul>
      <li><svg width="20" height="20" viewBox="0 0 20 20" fill="none" stroke="#fff" stroke-width="1.5"><path d="M4 2l3 1 1 4-2 1.5a10 10 0 0 0 5.5 5.5L13 12l4 1 1 3-2 2C9 18 2 11 2 4z"/></svg>(555) 014 2290</li>
      <li><svg width="22" height="16" viewBox="0 0 22 16" fill="none" stroke="#fff" stroke-width="1.5"><rect x="1" y="1" width="20" height="14"/><path d="M1 1l10 8 10-8"/></svg>info@northgatelegal.com</li>
    </ul></div>
  </div>
  <div class="footer-line"></div>
  <p class="copyright">© 2020 Company Name | All Rights Reserved</p>
</footer>

</body>
</html>
```